Business card design

We need a business card designed completed for a new company. We are a company that works with associations, schools to convert their older text/DVDs into dynamic online and mobile programs. Our initial platform is designed for the legal associations and will enable their lawyers to access their content such as forms, videos, case law and support materials anywhere, anytime. We are also focused on Project Management Associations, Financial Management Associations and IT Associations.

I would like for the business card to have the following information:

Logo

Kent marrowby

President and CEO

kmarrowby@trevantiq.example

Mobile: 555-374-9160

www.trevantiq.example

Tag line: Transforming content into a mobile platform    

I would like it to be double sided, use the colours of the logo, tie into the mobile world

 

Industry/Entity Type

Legal

Logo Text

Trevantiq

```html
<!DOCTYPE html>
<html lang="en">
<head>
<meta charset="utf-8">
<title>Trevantiq business card options</title>
<link rel="stylesheet" href="https://fonts.googleapis.com/css2?family=Open+Sans:wght@400&family=Questrial&family=Mulish:wght@700&display=swap">
<style>
  :root {
    --backdrop: #5b2f1f;
    --card: #939393;
    --card-edge: #7f7f7f;
    --ink-light: #ffffff;
    --ink-dark: #111111;
  }
  * { margin: 0; padding: 0; box-sizing: border-box; }
  html, body { width: 1200px; height: 309px; overflow: hidden; }
  body {
    position: relative;
    background: var(--backdrop);
    font-family: "Questrial", "Century Gothic", sans-serif;
    color: var(--ink-light);
  }
  .option-label {
    position: absolute;
    top: 22px;
    width: 200px;
    margin-left: -100px;
    text-align: center;
    font-family: "Open Sans", Arial, sans-serif;
    font-size: 19px;
  }
  .option-label--one { left: 219px; }
  .option-label--two { left: 597px; }
  .option-label--three { left: 981px; }

  .card {
    position: absolute;
    background: var(--card);
    border: 1px solid var(--card-edge);
    overflow: hidden;
  }
  .card--one { left: 34px; top: 60px; width: 358px; height: 204px; }
  .card--two { left: 419px; top: 60px; width: 356px; height: 203px; }
  .card--three { left: 803px; top: 63px; width: 356px; height: 203px; }

  .tagline-caps {
    position: absolute;
    left: 0; right: 0;
    text-transform: uppercase;
    letter-spacing: 2.6px;
    font-size: 16.5px;
    line-height: 26px;
    text-align: center;
  }
  .web-address {
    position: absolute;
    left: 0; right: 0;
    text-align: center;
    font-size: 12.5px;
    line-height: 14px;
    letter-spacing: 2.4px;
  }

  /* Option 1 */
  .card--one .tagline-caps { top: 78px; }
  .card--one .web-address { top: 180px; }

  /* Option 2 */
  .tagline-outlined {
    position: absolute;
    left: 13px;
    top: 81px;
    font-family: "Mulish", "Century Gothic", sans-serif;
    font-weight: 700;
    font-size: 18px;
    letter-spacing: 4px;
    line-height: 30px;
    white-space: nowrap;
    color: var(--ink-light);
    text-shadow: -1px -1px 0 var(--ink-dark), 1px -1px 0 var(--ink-dark),
                 -1px 1px 0 var(--ink-dark), 1px 1px 0 var(--ink-dark),
                 2px 2px 2px rgba(0,0,0,0.5);
  }
  .tagline-outlined .second-line { padding-left: 31px; }
  .card--two .web-address { top: 180px; }

  /* Option 3 */
  .brand-name {
    position: absolute;
    left: 0; right: 0;
    top: 38px;
    text-align: center;
    font-family: "Mulish", "Century Gothic", sans-serif;
    font-weight: 700;
    font-size: 60px;
    line-height: 70px;
    color: var(--ink-light);
  }
  .card--three .tagline-caps { top: 138px; line-height: 27px; }
</style>
</head>
<body>
  <div class="option-label option-label--one">Option # 1</div>
  <div class="option-label option-label--two">Option # 2</div>
  <div class="option-label option-label--three">Option # 3</div>

  <section class="card card--one" aria-label="Card option 1">
    <p class="tagline-caps">Transforming content into<br>a mobile platform</p>
    <p class="web-address">www.trevantiq.example</p>
  </section>

  <section class="card card--two" aria-label="Card option 2">
    <p class="tagline-outlined">Transforming Content Into<br><span class="second-line">A Mobile Platform</span></p>
    <p class="web-address">www.trevantiq.example</p>
  </section>

  <section class="card card--three" aria-label="Card option 3">
    <div class="brand-name">Trevantiq</div>
    <p class="tagline-caps">Transforming content into<br>a mobile platform</p>
  </section>
</body>
</html>
```